Cutting Edge Property Services Provider is Looking to Update Business Card Design

We are looking to freshen up our business cards to match our cutting edge technology based image.

KORVANEX - Where Care Finds Its Pulse

More information about our company can be found on our website at www.korvanex-demo.net

We integrate technology in a historically low tech industry.

We have appeared on the Brisk 300/3000 list 2 years in a row and we're previously recognized as the 5th Quickest Rising Firm in San Diego.

Our core colors are blue and white, but are not against accents that might improve our image.

We currently have our Mission Statement on our Business Cards in a folding design:
KORVANEX IS THE LEADING BUILDING SERVICES INNOVATOR. BY COMBINING TECHNOLOGY WITH FUNCTIONAL TOOS THAT IMPROVE EFFICIENCY IN THE WORKPLACE, WE PROVIDE UNPARALLELED SERVICE IN THE INDUSTRY. DEVELOPING LASTING RELATIONSHIPS WITH OUR CLIENTS AND ASSOCIATES IS THE CORNERSTONE OF OUR SUCCESS.

We'd like to convey the image of a cutting edge, technology based company. Want the cards to pop.

Target Market(s)

Commercial Property Managers - 20 to 50 year old professionals

Industry/Entity Type

Business

Requirements
Must have
• Must utilize our logo obviously, but are definitely open to using variations on the logo. Utilizing the components of the logo, but maybe in different configurations or backgrounds, etc...

Must use the Name: KORVANEX.
Can also use KORVANEX PROPERTY SERVICES.

Must include the Mission Statement

Must say: Where Care Finds Its Pulse
Nice to have
• We are considering plastic stock, shaped cards, or folding cards.

Nothing over the top or really expensive, but will consider if it conveys innovation and technology.
Should not have
• No images of toilets, buildings, trees, or anything relating to commercial properties.

We want to convey our technology image.

```html
<!DOCTYPE html>
<html lang="en">
<head>
<meta charset="utf-8">
<title>KORVANEX Business Card</title>
<link rel="stylesheet" href="https://fonts.googleapis.com/css2?family=Questrial&display=swap">
<style>
  :root {
    --brand-blue: #0e4a7c;
    --card-face: #f1f2f3;
    --card-edge: #d9dcdf;
    --ink-dark: #3c3f42;
    --swoosh-shadow: #5b5f63;
    --white: #ffffff;
    --backdrop: #e4e6e8;
  }
  * { box-sizing: border-box; margin: 0; padding: 0; }
  html, body { width: 1200px; height: 900px; overflow: hidden; }
  body {
    background: var(--backdrop);
    font-family: "Questrial", "Century Gothic", sans-serif;
    position: relative;
  }
  .card {
    position: absolute;
    width: 558px;
    height: 320px;
    border-radius: 22px;
    overflow: hidden;
    background: var(--card-face);
    box-shadow: 0 0 0 1px var(--card-edge), 0 10px 24px rgba(0,0,0,0.12);
  }
  .card--front { left: 388px; top: 45px; }
  .card--back { left: 225px; top: 408px; width: 561px; }
  .card__shape { position: absolute; inset: 0; }
  .brand {
    position: absolute;
    display: flex;
    align-items: center;
    gap: 12px;
    color: var(--brand-blue);
    font-size: 32px;
    letter-spacing: 2px;
  }
  .brand__mark { width: 22px; height: 22px; background: var(--brand-blue); }
  .card--front .brand { left: 66px; top: 112px; }
  .card--back .brand { left: 318px; top: 128px; }
  .address {
    position: absolute;
    color: var(--ink-dark);
    font-size: 15px;
    line-height: 22px;
    text-align: center;
  }
  .card--front .address { left: 92px; top: 255px; }
  .card--back .address { left: 338px; top: 268px; }
  .identity {
    position: absolute;
    right: 22px;
    top: 122px;
    color: var(--white);
    text-align: right;
  }
  .identity__name { font-size: 19px; line-height: 24px; }
  .identity__role { font-size: 14px; line-height: 20px; }
  .contacts {
    position: absolute;
    right: 22px;
    top: 199px;
    color: var(--white);
    font-size: 15px;
    line-height: 23.5px;
    text-align: right;
    list-style: none;
  }
  .tagline {
    position: absolute;
    right: 22px;
    top: 38px;
    color: var(--brand-blue);
    font-size: 16px;
  }
  .mission {
    position: absolute;
    left: 17px;
    top: 117px;
    color: var(--white);
    font-size: 14px;
    line-height: 18.7px;
    white-space: nowrap;
  }
  .mission span { display: block; }
</style>
</head>
<body>
  <section class="card card--front" aria-label="Card front">
    <svg class="card__shape" viewBox="0 0 558 320" aria-hidden="true">
      <path d="M400 0 C330 90 300 200 262 320" fill="none" stroke="var(--swoosh-shadow)" stroke-width="6"/>
      <path d="M404 0 C334 90 304 200 266 320" fill="none" stroke="var(--white)" stroke-width="4"/>
      <path d="M412 0 C342 90 312 200 274 320 L558 320 L558 0 Z" fill="var(--brand-blue)"/>
    </svg>
    <div class="brand"><span class="brand__mark"></span><span class="brand__name">KORVANEX</span></div>
    <p class="address">123, Abc Street<br>0000 City, Country</p>
    <div class="identity">
      <p class="identity__name">Your Name</p>
      <p class="identity__role">Designation</p>
    </div>
    <ul class="contacts">
      <li>cell : +12 345 67 8910</li>
      <li>phone : +12 345 67 8910</li>
      <li>email : info@yourwebsite.com</li>
      <li>web : www.yourwebsite.com</li>
    </ul>
  </section>

  <section class="card card--back" aria-label="Card back">
    <svg class="card__shape" viewBox="0 0 561 320" aria-hidden="true">
      <path d="M162 0 C242 60 292 180 312 320" fill="none" stroke="var(--swoosh-shadow)" stroke-width="5"/>
      <path d="M156 0 C236 60 286 180 306 320" fill="none" stroke="var(--white)" stroke-width="5"/>
      <path d="M0 0 L150 0 C230 60 280 180 300 320 L0 320 Z" fill="var(--brand-blue)"/>
    </svg>
    <p class="tagline">Where Care Finds Its Pulse</p>
    <div class="brand"><span class="brand__mark"></span><span class="brand__name">KORVANEX</span></div>
    <p class="mission">
      <span>Korvanex is the leading</span>
      <span>building services innovator.</span>
      <span>By combining technology with</span>
      <span>functional toos that improve</span>
      <span>efficiency in the workplace, we</span>
      <span>provide unparalleled service in</span>
      <span>the industry. Developing lasting</span>
      <span>relationships with our clients</span>
      <span>and associates is the</span>
      <span>cornerstone of our success.</span>
    </p>
    <p class="address">123, Abc Street<br>0000 City, Country</p>
  </section>
</body>
</html>
```